Marwick Law Letterhead

We need a new letterhead design for a Law Firm. The address for the law firm is 1475 Calloway Street, Suite 210, Houston, Texas 77041. Phone Number: 832-361-9027; Fax Number: 832-614-7359. The logo is uploaded to the project.

```html
<!DOCTYPE html>
<html lang="en">
<head>
<meta charset="utf-8">
<title>Marwick Law Letterhead</title>
<link href="https://fonts.googleapis.com/css2?family=Montserrat:wght@400;500;600&display=swap" rel="stylesheet">
<style>
  :root {
    --backdrop: #e9e9e9;
    --paper: #ffffff;
    --red: #d0161f;
    --red-dark: #7a0610;
    --navy: #1d2d5c;
    --ink: #2a2a2a;
    --signature-tone: #c9c9c9;
  }
  * { margin: 0; padding: 0; box-sizing: border-box; }
  html, body {
    width: 1154px; height: 1200px; overflow: hidden;
    background: var(--backdrop);
    font-family: "Montserrat", sans-serif;
    color: var(--ink);
  }
  .letterhead {
    position: absolute; left: 162px; top: 20px;
    width: 830px; height: 1160px;
    background: var(--paper);
    overflow: hidden;
    box-shadow: 0 6px 24px rgba(0,0,0,0.18);
  }
  .corner-sweep { position: absolute; left: 0; top: 0; }
  .brand {
    position: absolute; left: 318px; top: 92px;
    display: flex; align-items: center; gap: 12px;
  }
  .brand-mark { width: 22px; height: 22px; background: var(--red); }
  .brand-name {
    font-size: 30px; font-weight: 600; color: var(--navy);
    letter-spacing: 0.5px;
  }
  .contact-divider {
    position: absolute; left: 621px; top: 64px;
    width: 1.5px; height: 97px; background: var(--red);
  }
  .contact {
    position: absolute; left: 634px; top: 62px;
    font-size: 14px; line-height: 18px; color: #111;
  }
  .contact-address { margin-bottom: 11px; }
  .contact-line { display: flex; align-items: center; gap: 9px; line-height: 21px; }
  .contact-line svg { width: 13px; height: 13px; }
  .header-rule {
    position: absolute; left: 30px; top: 198px;
    width: 769px; height: 2px; background: var(--red);
  }
  .recipient {
    position: absolute; left: 31px; top: 266px;
    font-size: 13.5px; line-height: 20.6px;
  }
  .letter-body {
    position: absolute; left: 32px; top: 354px; width: 769px;
    font-size: 13.5px; line-height: 20.6px; text-align: justify;
  }
  .letter-body p { margin-bottom: 20.6px; }
  .sign-off {
    position: absolute; left: 30px; top: 934px;
    font-size: 17px;
  }
  .signature {
    position: absolute; left: 30px; top: 966px;
    width: 94px; height: 28px;
    background: linear-gradient(90deg, var(--signature-tone), #e4e4e4);
    border-radius: 3px;
  }
</style>
</head>
<body>
  <main class="letterhead">
    <svg class="corner-sweep" width="830" height="1160" viewBox="0 0 830 1160" aria-hidden="true">
      <defs>
        <linearGradient id="sweep-top" x1="0" y1="0" x2="1" y2="0">
          <stop offset="0" stop-color="#d0161f"/>
          <stop offset="1" stop-color="#7a0610"/>
        </linearGradient>
        <linearGradient id="sweep-bottom" x1="0" y1="0" x2="1" y2="0">
          <stop offset="0" stop-color="#d0161f"/>
          <stop offset="1" stop-color="#7a0610"/>
        </linearGradient>
      </defs>
      <path d="M0 0 H322 Q130 60 0 192 Z" fill="url(#sweep-top)"/>
      <path d="M830 963 V1160 H494 Q730 1090 830 963 Z" fill="url(#sweep-bottom)"/>
    </svg>

    <div class="brand">
      <span class="brand-mark"></span>
      <span class="brand-name">Marwick Law</span>
    </div>

    <div class="contact-divider"></div>
    <div class="contact">
      <div class="contact-address">1475 Calloway Street,<br>Suite 210, Houston,<br>Texas 77041</div>
      <div class="contact-line">
        <svg viewBox="0 0 24 24" aria-hidden="true"><path fill="#d0161f" d="M6.6 10.8a15.1 15.1 0 0 0 6.6 6.6l2.2-2.2c.3-.3.7-.4 1-.2 1.1.4 2.3.6 3.6.6.6 0 1 .4 1 1V20c0 .6-.4 1-1 1A17 17 0 0 1 3 4c0-.6.4-1 1-1h3.5c.6 0 1 .4 1 1 0 1.3.2 2.5.6 3.6.1.3 0 .7-.2 1z"/></svg>
        <span>832-361-9027</span>
      </div>
      <div class="contact-line">
        <svg viewBox="0 0 24 24" aria-hidden="true"><path fill="#d0161f" d="M6 2h12v5H6zM3 8h18a1 1 0 0 1 1 1v8h-4v5H6v-5H2V9a1 1 0 0 1 1-1zm5 8v4h8v-4z"/></svg>
        <span>832-614-7359</span>
      </div>
    </div>

    <div class="header-rule"></div>

    <address class="recipient" style="font-style:normal">
      Mr/s<br>First Name and Last Name<br>Company Name<br>Address
    </address>

    <section class="letter-body">
      <p>Lorem ipsum dolor sit amet,consectetur adipiscing sed do eiusmod tempor incididunt laboreet dolore magna aliqua.Ut enim ad minim.veniam, quis nostrud exercitation ullamco laboris nisi ut aliquip exea commodo consequat.Lorem ipsum dolor sit amet,consectetur adipiscing sed do eiusmod tempor incididunt.labore et dolore magna aliqua. Ut enim</p>
      <p>Lorem ipsum dolor sit amet, consectetur adipiscing sed do eiusmod tempor incididunt labore et dolore magna aliqua. Ut enim ad minim veniam, quis nostrud exercitation ullamco laboris nisi ut aliquip exea commodo consequat.Duis aute irure dolor in reprehenderit in voluptate velit esse cillum irure dolor in reprehenderit in voluptate velit esse irure</p>
      <p>Lorem ipsum dolor sit amet, consectetur adipiscing sed do eiusmod tempor incididunt labore et dolore magna aliqua. consequat. Duis aute irure dolor in.reprehenderit in voluptate velit esse cillum dolore eu fugiat nulla pariatur. Excepteur sint occaecat cupidatat non proident, sunt in culpa qui officia deserunt mollit,</p>
      <p>Lorem ipsum dolor sit amet, consectetur adipiscing sed do eiusmod tempor incididunt labore et dolore magna aliqua. Ut enim Lorem ipsum dolor sit amet, consectetur adipiscing sed do eiusmod tempor incididunt labore et dolore magna aliqua. Ut enim Lorem ipsum aliqua.ipsum</p>
      <p>Lorem ipsum dolor sit amet, consectetur adipiscing sed do eiusmod tempor incididunt labore et dolore magna aliqua. Ut enim ad minim veniam, quis nostrud exercitation ullamco laboris nisi ut aliquip exea commodo consequat.Duis aute irure dolor in reprehenderit in voluptate velit esse cillum irure dolor in reprehenderit in voluptate velit esse irure</p>
      <p>Lorem ipsum dolor sit amet, consectetur adipiscing sed do eiusmod tempor incididunt labore et dolore magna aliqua. Ut enim ad minim veniam, quis nostrud exercitation ullamco laboris nisi ut aliquip exea commodo consequat.Duis aute irure dolor in reprehenderit in voluptate velit esse cillum irure dolor in reprehenderit in voluptate velit esse irure</p>
    </section>

    <div class="sign-off">Regards</div>
    <div class="signature" role="img" aria-label="Handwritten signature of the sender"></div>
  </main>
</body>
</html>
```